letterhead design using our existing logo

We are a small boutique property management business based in Sydney's Northern Beaches.
We are after a sleek, simple modern letterhead (A4) incorporating our logo and its colours.
Also matching envelope (DL)
I have attached the logo with black text and white text for design options.

Target Market(s)

29-69yo Male and Female

Industry/Entity Type

Property Management

Requirements
Must have
• - Harbourline Estates logo
• - Address, number and website:
• Suite 7, 12-14 Wattlegrove Parade, Manly NSW 2095
• Tel: Carl Dorsey 0491 570 163 Marisol Quade 0491 570 218 www.harbourlinestatesgroup.com.au
Nice to have
• sleek design that looks modern and professional
Should not have
• too many colours or too busy

```html
<!DOCTYPE html>
<html lang="en">
<head>
<meta charset="utf-8">
<title>Harbourline Estates – Stationery</title>
<link href="https://fonts.googleapis.com/css2?family=Carlito:wght@400;700&family=Roboto+Condensed:wght@400;700&display=swap" rel="stylesheet">
<style>
  :root {
    --backdrop: #a5a5a5;
    --paper: #ffffff;
    --ink: #1a1a1a;
    --teal: #137a8c;
    --teal-light: #2aa0a8;
    --teal-text: #1a8a96;
    --rule: #7a6f8a;
    --sig: #d9e4e6;
  }
  * { margin: 0; padding: 0; box-sizing: border-box; }
  html, body { width: 1200px; height: 906px; overflow: hidden; background: var(--backdrop); }
  .stage { position: relative; width: 1200px; height: 906px; }
  address { font-style: normal; }

  .brand-name {
    font-family: "Roboto Condensed", sans-serif;
    font-weight: 700;
    white-space: nowrap;
    letter-spacing: 0.2px;
  }

  /* Letterhead (A4) */
  .letterhead {
    position: absolute; left: 47px; top: 98px; width: 508px; height: 719px;
    background: var(--paper);
  }
  .letterhead .brand-name {
    position: absolute; left: 46px; top: 47px; font-size: 19px; color: var(--ink);
  }
  .contact-block {
    position: absolute; left: 339px; top: 28px; height: 64px;
    border-left: 1px solid var(--rule); padding-left: 11px;
    font-family: "Roboto Condensed", sans-serif; font-size: 7px; color: #333; line-height: 8.5px;
  }
  .contact-block .row { display: flex; align-items: center; gap: 3px; }
  .contact-block svg { width: 6px; height: 6px; fill: var(--teal); flex: none; }
  .contact-block .group { margin-bottom: 7px; }
  .contact-block .address { color: var(--teal-text); }

  .letter-content {
    position: absolute; left: 50px; top: 134px; width: 426px;
    font-family: "Carlito", sans-serif; font-size: 9.3px; line-height: 18px; color: var(--ink);
  }
  .letter-content p { margin-bottom: 18px; }
  .letter-content .letter-heading { font-weight: 700; margin-bottom: 18px; }
  .letter-content .closing { margin-bottom: 0; }
  .signature {
    width: 126px; height: 42px; margin: 2px 0 10px -5px;
    background: linear-gradient(90deg, var(--sig), #eef3f4);
    border-radius: 3px;
  }
  .letter-footer { position: absolute; left: 0; bottom: 0; width: 508px; height: 19px; display: block; }

  /* DL envelope, front */
  .envelope-front {
    position: absolute; left: 595px; top: 141px; width: 571px; height: 285px;
    background: var(--paper);
  }
  .envelope-sender {
    position: absolute; left: 22px; top: 236px;
    display: flex; align-items: center; gap: 9px;
  }
  .envelope-sender .brand-name { font-size: 14.5px; color: var(--ink); }
  .return-address {
    border-left: 1px solid var(--rule); padding-left: 6px;
    font-family: "Roboto Condensed", sans-serif; font-size: 8px; line-height: 11px; color: #333;
  }

  /* DL envelope, back */
  .envelope-back {
    position: absolute; left: 596px; top: 486px; width: 565px; height: 284px;
    background: var(--paper);
  }
  .envelope-flap { position: absolute; left: 0; top: 0; width: 565px; height: 92px; display: block; }
  .envelope-back .brand-name {
    position: absolute; left: 0; right: 0; top: 37px; text-align: center;
    font-size: 13px; color: #ffffff;
  }
</style>
</head>
<body>
<main class="stage">

  <section class="letterhead" aria-label="A4 letterhead">
    <div class="brand-name">HARBOURLINE ESTATES</div>

    <address class="contact-block">
      <div class="group">
        <div class="row"><svg viewBox="0 0 10 10"><path d="M1 4 Q5 0 9 4 L8 5 L6 4 L6 3 L4 3 L4 4 L2 5 Z M2 6 H8 V8 H2 Z"/></svg>0491 570 163 (Carl Dorsey)</div>
        <div class="row"><svg viewBox="0 0 10 10"><path d="M1 4 Q5 0 9 4 L8 5 L6 4 L6 3 L4 3 L4 4 L2 5 Z M2 6 H8 V8 H2 Z"/></svg>0491 570 218 (Marisol Quade)</div>
      </div>
      <div class="group">
        <div class="row"><svg viewBox="0 0 10 10"><path d="M1 2 H9 V8 H1 Z M1 2 L5 5 L9 2" fill="none" stroke="#137a8c" stroke-width="1.2"/></svg>info@harbourlinestatesgroup.com.au</div>
        <div class="row"><svg viewBox="0 0 10 10"><circle cx="5" cy="5" r="3.8" fill="none" stroke="#137a8c" stroke-width="1.2"/><path d="M1 5 H9 M5 1 V9" stroke="#137a8c" stroke-width="0.8"/></svg>www.harbourlinestatesgroup.com.au</div>
      </div>
      <div class="address">Suite 7, 12-14 Wattlegrove Parade<br>Manly NSW 2095</div>
    </address>

    <div class="letter-content">
      <p class="letter-heading">Lorem Ipsum is simply</p>
      <p>&nbsp;dummy text of the printing and typesetting industry. Lorem Ipsum has been the industry's standard dummy text ever since the 1500s, when an unknown printer took a galley of type and scrambled it to make a type specimen book. It has survived not only five centuries, but also the leap into electronic typesetting, remaining essentially unchanged.</p>
      <p>It is a long established fact that a reader will be distracted by the readable content of a page when looking at its layout. The point of using Lorem Ipsum is that it has a more-or-less normal distribution of letters, as opposed to using 'Content here, content here', making it look like readable English. Many desktop publishing packages and web page editors now use Lorem Ipsum as their default model text, and a search for 'lorem ipsum' will uncover many web sites still in their infancy. Various versions have evolved over the years, sometimes by accident, sometimes on purpose (injected humour and the like).</p>
      <p>&nbsp;Contrary to popular belief, Lorem Ipsum is not simply random text. It has roots in a piece of classical Latin literature from 45 BC, making it over 2000 years old. Edwin Harrowgate, a Latin professor at Ashgrove Hill College in Virginia, looked up one of the more obscure Latin words, consectetur, from a Lorem Ipsum passage,</p>
      <p class="closing">Lorem Ipsum</p>
      <div class="signature" role="img" aria-label="Handwritten signature"></div>
      <p class="sign-off">Lorem Ipsum is a dummy</p>
    </div>

    <svg class="letter-footer" viewBox="0 0 508 19" preserveAspectRatio="none" aria-hidden="true">
      <path d="M0 0 H300 Q340 2 370 19 H0 Z" fill="var(--teal-light)"/>
      <path d="M318 0 H508 V19 H382 Q355 3 318 0 Z" fill="var(--teal)"/>
    </svg>
  </section>

  <section class="envelope-front" aria-label="DL envelope front">
    <div class="envelope-sender">
      <div class="brand-name">HARBOURLINE ESTATES</div>
      <address class="return-address">Suite 7, 12-14 Wattlegrove Parade<br>Manly NSW 2095</address>
    </div>
  </section>

  <section class="envelope-back" aria-label="DL envelope back">
    <svg class="envelope-flap" viewBox="0 0 565 92" preserveAspectRatio="none" aria-hidden="true">
      <path d="M0 0 H565 L556 80 Q554 91 544 91 H21 Q11 91 9 80 Z" fill="var(--teal)"/>
    </svg>
    <div class="brand-name">HARBOURLINE ESTATES</div>
  </section>

</main>
</body>
</html>
```